Business Card design for insurance broker in Denver, CO, USA

I need a business card designed using this logo that was just created. We sell life and disability income insurance to US consumers.
Looking for a professionally designed card to make use of the logo and have something to hand to prospects or new business referral sources. The card could be white, gray, black or whatever you would recommend.

Target Market(s)

US Consumers and other financial professionals that I partner with.

Industry/Entity Type

Insurance Broker

Contact Information for Business Card

Owen T. Farrow, CLU, LUTCF (please note that CLU should have a superscript R in a circle for registered trademark)
President
phone (303) 555-0187
email owen@keelbrookcover.example
4620 W. Halvern Rd, Suite 300, Brightfield Village, CO 80199
Somewhere fit in a tagline saying "Your resource for life, long term care, and disability insurance" (maybe the back if it doesn't fit on the front, your call)

Font styles to use
Sans Serif

Requirements
Must have
• Must have logo in correct blue and gray colors, my name, address, phone, email. Order and placement determined by the designer.
• I just want something that looks a more professional than what I could have done using the business card designer tool on pixelbazaar.example or QuillPress, or any other do-it-yourself tool
• A regular rectangular business card with square corners is preferred
Nice to have
• I included the logos of 2 organizations I belong to (GKLS and WOBCE). They should be small, but visible on the back only. If it doesn’t look good, this is not a requirement, feel free to drop it.
Should not have
• Do not add any colors not already in the logo, except use of black and whites which are okay. If you use the logo on the back and want to make that in all black, gray or white, that may be okay as well.

```html
<!DOCTYPE html>
<html lang="en">
<head>
<meta charset="utf-8">
<title>Keelbrook Insurance Solutions – Business Card</title>
<link rel="stylesheet" href="https://fonts.googleapis.com/css2?family=Montserrat:wght@400;500;600;700&display=swap">
<style>
  :root {
    --brand-blue: #1b7fc0;
    --brand-gray: #7d7f82;
    --ink-soft: #6b6d70;
    --paper: #ffffff;
    --backdrop: #e6eaf0;
    --badge-tint: #5aa6d8;
    --watermark: #eef0f2;
  }
  * { box-sizing: border-box; margin: 0; padding: 0; }
  html, body { width: 1200px; height: 675px; overflow: hidden; }
  body {
    background: var(--backdrop);
    font-family: "Montserrat", sans-serif;
    position: relative;
  }
  .card {
    position: absolute;
    top: 189px;
    width: 520px;
    height: 297px;
    overflow: hidden;
    box-shadow: 0 6px 18px rgba(40, 60, 90, 0.18);
  }
  .card--front { left: 60px; background: var(--paper); }
  .card--back { left: 620px; background: var(--brand-blue); }

  .watermark-ring {
    position: absolute;
    left: 150px; top: 40px;
    width: 220px; height: 220px;
    border: 14px solid var(--watermark);
    border-radius: 50%;
  }

  .wordmark { position: absolute; display: flex; align-items: center; gap: 10px; }
  .wordmark__dot { border-radius: 50%; border: 3px solid currentColor; flex: none; }
  .wordmark__name { font-weight: 700; text-transform: uppercase; line-height: 1.05; letter-spacing: 0.02em; }

  .card--front .wordmark { right: 22px; top: 26px; color: var(--brand-blue); }
  .card--front .wordmark__dot { width: 40px; height: 40px; }
  .card--front .wordmark__name { font-size: 15px; }

  .rule { position: absolute; height: 2px; background: var(--brand-blue); }
  .rule--top { left: 250px; right: 20px; top: 86px; }
  .rule--mid { left: 20px; right: 20px; top: 158px; }
  .rule--low { left: 20px; right: 20px; top: 238px; }

  .person { position: absolute; left: 26px; top: 104px; color: var(--brand-blue); }
  .person__name { font-size: 15px; font-weight: 700; }
  .person__name sup { font-size: 8px; }
  .person__role { font-size: 12px; font-weight: 700; letter-spacing: 0.32em; margin-top: 4px; text-transform: uppercase; }

  .contact { position: absolute; display: flex; flex-direction: column; gap: 10px; font-size: 9.5px; color: var(--ink-soft); }
  .contact--web { right: 22px; top: 104px; }
  .contact--place { left: 26px; top: 172px; }
  .contact__item { display: flex; align-items: center; gap: 8px; line-height: 1.25; }
  .contact__icon { width: 13px; height: 13px; flex: none; fill: var(--brand-blue); }

  .tagline {
    position: absolute; left: 0; right: 0; top: 249px;
    text-align: center; color: var(--brand-blue);
    font-size: 11.5px; font-weight: 700; letter-spacing: 0.1em;
    text-transform: uppercase; line-height: 1.35;
  }

  .card--back .wordmark { left: 44px; top: 118px; color: var(--paper); gap: 14px; }
  .card--back .wordmark__dot { width: 62px; height: 62px; border-width: 4px; }
  .card--back .wordmark__name { font-size: 22px; }

  .member-badge { position: absolute; background: var(--badge-tint); opacity: 0.75; }
  .member-badge--upper { right: 40px; top: 40px; width: 110px; height: 56px; border-radius: 6px; }
  .member-badge--lower { right: 52px; top: 170px; width: 86px; height: 86px; border-radius: 50%; }
</style>
</head>
<body>

<section class="card card--front" aria-label="Business card front">
  <div class="watermark-ring" aria-hidden="true"></div>

  <div class="wordmark">
    <span class="wordmark__dot" aria-hidden="true"></span>
    <span class="wordmark__name">Keelbrook<br>Insurance Solutions</span>
  </div>
  <div class="rule rule--top"></div>

  <div class="person">
    <p class="person__name">Owen T. Farrow, CLU<sup>®</sup>, LUTCF</p>
    <p class="person__role">President</p>
  </div>

  <div class="contact contact--web">
    <p class="contact__item">
      <svg class="contact__icon" viewBox="0 0 16 16" aria-hidden="true"><path d="M1 3h14v10H1z M1 3l7 6 7-6" fill="none" stroke="#1b7fc0" stroke-width="1.6"/></svg>
      owen@keelbrookcover.example
    </p>
    <p class="contact__item">
      <svg class="contact__icon" viewBox="0 0 16 16" aria-hidden="true"><circle cx="8" cy="8" r="6.5" fill="none" stroke="#1b7fc0" stroke-width="1.5"/><path d="M1.5 8h13M8 1.5c-3 3.5-3 9.5 0 13M8 1.5c3 3.5 3 9.5 0 13" fill="none" stroke="#1b7fc0" stroke-width="1.2"/></svg>
      www.keelbrookcover.example
    </p>
  </div>
  <div class="rule rule--mid"></div>

  <div class="contact contact--place">
    <p class="contact__item">
      <svg class="contact__icon" viewBox="0 0 16 16" aria-hidden="true"><path d="M8 1a5 5 0 0 0-5 5c0 4 5 9 5 9s5-5 5-9a5 5 0 0 0-5-5zm0 7a2 2 0 1 1 0-4 2 2 0 0 1 0 4z"/></svg>
      <span>4620 W. Halvern Rd, Suite 300,<br>Brightfield Village, CO 80199</span>
    </p>
    <p class="contact__item">
      <svg class="contact__icon" viewBox="0 0 16 16" aria-hidden="true"><path d="M3.5 1.5l2.5 0 1.2 3.3-1.7 1.2a8 8 0 0 0 4.5 4.5l1.2-1.7 3.3 1.2v2.5c0 .8-.7 1.5-1.5 1.5C6.5 14 2 9.5 2 3c0-.8.7-1.5 1.5-1.5z"/></svg>
      (303) 555-0187
    </p>
  </div>
  <div class="rule rule--low"></div>

  <p class="tagline">Your resource for life, long term care,<br>and disability insurance</p>
</section>

<section class="card card--back" aria-label="Business card back">
  <div class="wordmark">
    <span class="wordmark__dot" aria-hidden="true"></span>
    <span class="wordmark__name">Keelbrook<br>Insurance Solutions</span>
  </div>
  <div class="member-badge member-badge--upper" role="img" aria-label="WOBCE membership badge"></div>
  <div class="member-badge member-badge--lower" role="img" aria-label="GKLS membership badge"></div>
</section>

</body>
</html>
```